One business card required with 2 company logos and 2 people's details

One business card required.
No preference on design - One side could show the 2 different business logos for the companies we own. The reverse could have the details shown below.
Another option could be one business one side and one business on the reverse. Happy to receive designs.

Dora Pellham
07700 913 286
Rowena Tindall
07700 958 137

website: quietmeadowbloom.co.uk
email: info@quietmeadowbloom.co.uk

website: brightharbourevents.co.uk
email: info:brightharbourevents.co.uk

May be nice to have icons instead of the words email/website?

I have included different versions of the logos to help with your design.

Contact Information for Business Card

see project overview

Requirements
Must have
• both company logos, both contact names and contact details

```html
<!DOCTYPE html>
<html lang="en">
<head>
<meta charset="utf-8">
<title>Business cards – Quiet Meadow Bloom &amp; Bright Harbour Events</title>
<link href="https://fonts.googleapis.com/css2?family=Roboto:wght@400;500;700&display=swap" rel="stylesheet">
<style>
  :root {
    --page-bg: #202020;
    --card-bg: #ffffff;
    --ink-light: #ffffff;
    --brand-navy: #1c2a5e;
    --brand-blue: #0a5fd0;
  }
  * { margin: 0; padding: 0; box-sizing: border-box; }
  html, body { width: 1200px; height: 1200px; overflow: hidden; }
  body {
    background: var(--page-bg);
    font-family: "Roboto", Arial, sans-serif;
    position: relative;
  }
  .card {
    position: absolute;
    left: 257px;
    width: 686px;
    height: 392px;
    border-radius: 19px;
    background: var(--card-bg);
    overflow: hidden;
  }
  .card--meadow { top: 165px; }
  .card--harbour { top: 653px; }
  .card__wave {
    position: absolute;
    inset: 0;
    width: 100%;
    height: 100%;
  }
  .contacts {
    position: absolute;
    left: 37px;
    top: 222px;
    color: var(--ink-light);
  }
  .contacts__name {
    font-size: 23px;
    font-weight: 700;
    line-height: 28px;
    letter-spacing: -0.2px;
  }
  .contacts__line {
    display: flex;
    align-items: center;
    gap: 5px;
    font-size: 15.5px;
    line-height: 20px;
  }
  .contacts__line--phone { font-weight: 500; margin-bottom: 1px; }
  .contacts__web { margin-top: 8px; }
  .contacts__line svg { width: 14px; height: 14px; flex: none; fill: var(--ink-light); }
  .brand {
    position: absolute;
    left: 420px;
    width: 200px;
    text-align: center;
    font-family: "Roboto", Arial, sans-serif;
    font-weight: 500;
    font-size: 29px;
    line-height: 33px;
  }
  .brand--meadow { top: 118px; color: var(--brand-navy); }
  .brand--harbour { top: 124px; color: var(--brand-blue); }
</style>
</head>
<body>

<svg width="0" height="0" style="position:absolute" aria-hidden="true">
  <defs>
    <radialGradient id="wave-fill" cx="0.55" cy="0.7" r="0.6">
      <stop offset="0" stop-color="#0a8ccc"/>
      <stop offset="0.55" stop-color="#0866c0"/>
      <stop offset="1" stop-color="#0637a8"/>
    </radialGradient>
    <linearGradient id="stripe-meadow" x1="0" y1="0" x2="1" y2="0">
      <stop offset="0" stop-color="#1c4fc0"/>
      <stop offset="0.5" stop-color="#7b52e8"/>
      <stop offset="0.72" stop-color="#2a4fcc"/>
      <stop offset="1" stop-color="#4fd8e0"/>
    </linearGradient>
    <linearGradient id="stripe-harbour" x1="0" y1="0" x2="1" y2="0">
      <stop offset="0" stop-color="#0a4fc8"/>
      <stop offset="1" stop-color="#0a78ea"/>
    </linearGradient>
    <symbol id="icon-phone" viewBox="0 0 24 24"><path d="M6.6 10.8c1.4 2.8 3.8 5.1 6.6 6.6l2.2-2.2c.3-.3.7-.4 1-.2 1.1.4 2.3.6 3.6.6.6 0 1 .4 1 1V20c0 .6-.4 1-1 1C10.6 21 3 13.4 3 4c0-.6.4-1 1-1h3.5c.6 0 1 .4 1 1 0 1.3.2 2.5.6 3.6.1.3 0 .7-.2 1l-2.3 2.2z"/></symbol>
    <symbol id="icon-mail" viewBox="0 0 24 24"><path d="M2 5h20v14H2V5zm2 2v.3l8 5.4 8-5.4V7H4zm16 2.7l-8 5.4-8-5.4V17h16V9.7z"/></symbol>
    <symbol id="icon-globe" viewBox="0 0 24 24"><path d="M12 2a10 10 0 100 20 10 10 0 000-20zm-1 17.9A8 8 0 014.2 10.2L9 15v1c0 1.1.9 2 2 2v1.9zm6.9-2.5c-.3-.8-1-1.4-1.9-1.4h-1v-3c0-.6-.4-1-1-1H8v-2h2c.6 0 1-.4 1-1V7h2c1.1 0 2-.9 2-2v-.4a8 8 0 012.9 12.8z"/></symbol>
  </defs>
</svg>

<section class="card card--meadow" aria-label="Quiet Meadow Bloom card">
  <svg class="card__wave" viewBox="0 0 800 457" preserveAspectRatio="none" aria-hidden="true">
    <path d="M0,457 L0,240 C30,205 70,190 110,190 C200,190 300,240 430,310 C540,370 620,440 690,457 Z" fill="url(#wave-fill)"/>
    <path d="M105,189 C200,186 320,240 450,305 C560,360 660,412 800,426 L800,448 C690,442 590,400 465,332 C340,262 220,196 105,189 Z" fill="url(#stripe-meadow)"/>
  </svg>
  <div class="brand brand--meadow">Quiet Meadow Bloom</div>
  <div class="contacts">
    <p class="contacts__name">Rowena Tindall</p>
    <p class="contacts__line contacts__line--phone"><svg><use href="#icon-phone"/></svg>07700 958 137</p>
    <p class="contacts__name">Dora Pellham</p>
    <p class="contacts__line contacts__line--phone"><svg><use href="#icon-phone"/></svg>07700 913 286</p>
    <p class="contacts__line contacts__web"><svg><use href="#icon-mail"/></svg>info@quietmeadowbloom.co.uk</p>
    <p class="contacts__line"><svg><use href="#icon-globe"/></svg>quietmeadowbloom.co.uk</p>
  </div>
</section>

<section class="card card--harbour" aria-label="Bright Harbour Events card">
  <svg class="card__wave" viewBox="0 0 800 457" preserveAspectRatio="none" aria-hidden="true">
    <path d="M0,457 L0,240 C30,205 70,190 110,190 C200,190 300,240 430,310 C540,370 620,440 690,457 Z" fill="url(#wave-fill)"/>
    <path d="M105,189 C200,186 320,240 450,305 C560,360 660,412 800,426 L800,448 C690,442 590,400 465,332 C340,262 220,196 105,189 Z" fill="url(#stripe-harbour)"/>
  </svg>
  <div class="brand brand--harbour">Bright Harbour Events</div>
  <div class="contacts">
    <p class="contacts__name">Rowena Tindall</p>
    <p class="contacts__line contacts__line--phone"><svg><use href="#icon-phone"/></svg>07700 958 137</p>
    <p class="contacts__name">Dora Pellham</p>
    <p class="contacts__line contacts__line--phone"><svg><use href="#icon-phone"/></svg>07700 913 286</p>
    <p class="contacts__line contacts__web"><svg><use href="#icon-mail"/></svg>info@brightharbourevents.co.uk</p>
    <p class="contacts__line"><svg><use href="#icon-globe"/></svg>brightharbourevents.co.uk</p>
  </div>
</section>

</body>
</html>
```